Design eines Zertifikats
Ich bin total begeistert. Super Kommunikation, super schnelle Reaktion auf kleine Änderungswünsche, ich bin wirklich rundum zufrieden!! Auch bei weiterführenden Fragen die gar nicht direkt mit dem Design zusammenhingen wurde mir total schnell und sympathisch geholfen, ich kann die Designerin nur wärmstens weiterempfehlen!
Zielgruppe
Ich betreibe einen Onlineshop, in dem ich sogenannte Sterntaufen verkaufe. Ein Kunde bekommt dabei im Zuge seines Kaufes ein Zertifikat ausgestellt mit Daten zu seinem getauften Stern. Es geht hier um das Design eines neuen Zertifikats um möglichst noch mehr Käufer anzusprechen. Es sind bereits 3 Designs vorhanden, das neue sollte sich entsprechend etwas absetzen.
Ich lasse die Zertifikate in einer Druckerei drucken, und bedrucke diese dann selber mit den Daten der Sterntaufe, es muss auf dem Zertifikat also ein heller Bereich vorhanden sein in dem ich drucken kann.
Aufgabenstellung
Das Zertifikat soll A4 sein. Es sollte modern sein und sich wie gesagt möglichst von den bestehenden absetzen, und ein möglichst breites Publikum ansprechen.
Beispiele für Zertifikate der Konkurrenz finden sich unter:
himmelspunkt17.de
nebelverzeichnis.de
lichtpate-bundesweit.de
Das von himmelspunkt17.de gefällt mir persönlich ganz gut, aber lasst euch nicht von den Vorschlägen einschränken.
Bitte nicht zu exzessiv kostenpflichtiges Stockmaterial verwenden, ich mache leider aktuell noch Miese mit dem Shop :-)
Bitte schaut auf meine Webseite um ein Gefühl dafür zu bekommen wie viel Platz für Text vorhanden sein muss.

```html
<!DOCTYPE html>
<html lang="de">
<head>
<meta charset="utf-8">
<title>Sternzertifikat</title>
<link href="https://fonts.googleapis.com/css2?family=Great+Vibes&family=Montserrat:wght@300;500&display=swap" rel="stylesheet">
<style>
  :root {
    --night-deep: #0d1430;
    --night-blue: #1e2c66;
    --night-violet: #4a4a8f;
    --horizon-amber: #7a5a3a;
    --paper: #ffffff;
    --ink: #111111;
    --brand-navy: #27306e;
    --rule: #555555;
  }
  html, body {
    margin: 0;
    padding: 0;
    width: 1200px;
    height: 840px;
    overflow: hidden;
    background: var(--paper);
  }
  .certificate {
    position: relative;
    width: 1200px;
    height: 840px;
    overflow: hidden;
  }
  .certificate__sky,
  .certificate__sheet {
    position: absolute;
    inset: 0;
  }
  .certificate__content {
    position: absolute;
    inset: 0;
    font-family: "Montserrat", sans-serif;
    color: var(--ink);
  }
  .brand {
    position: absolute;
    left: 413px;
    top: 192px;
    transform: translateX(-50%);
    display: flex;
    align-items: center;
    gap: 8px;
    font-weight: 500;
    font-size: 16px;
    color: var(--brand-navy);
    letter-spacing: 0.04em;
  }
  .brand__dot {
    width: 12px;
    height: 12px;
    border-radius: 50%;
    background: var(--brand-navy);
  }
  .title {
    position: absolute;
    left: 420px;
    top: 228px;
    transform: translateX(-50%);
    margin: 0;
    font-family: "Great Vibes", cursive;
    font-weight: 400;
    font-size: 118px;
    line-height: 1;
    white-space: nowrap;
  }
  .title-rule {
    position: absolute;
    left: 272px;
    top: 418px;
    width: 314px;
    height: 0;
    border-top: 1px solid var(--rule);
  }
  .statement,
  .register {
    position: absolute;
    left: 457px;
    transform: translateX(-50%);
    margin: 0;
    font-weight: 300;
    font-size: 24.5px;
    line-height: 32px;
    text-align: center;
    white-space: nowrap;
  }
  .statement { top: 485px; }
  .register { top: 706px; }
</style>
</head>
<body>
<main class="certificate">
  <svg class="certificate__sky" width="1200" height="840" viewBox="0 0 1200 840" role="img" aria-label="Fotografie eines Sternenhimmels mit Milchstraße">
    <defs>
      <linearGradient id="skyTone" x1="0" y1="0" x2="1" y2="1">
        <stop offset="0" stop-color="#0c1536"/>
        <stop offset="0.45" stop-color="#1d2a63"/>
        <stop offset="0.72" stop-color="#3f3f86"/>
        <stop offset="1" stop-color="#7b5a36"/>
      </linearGradient>
    </defs>
    <rect width="1200" height="840" fill="url(#skyTone)"/>
  </svg>
  <svg class="certificate__sheet" width="1200" height="840" viewBox="0 0 1200 840" aria-hidden="true">
    <circle cx="332" cy="872" r="750" fill="var(--paper)"/>
  </svg>
  <div class="certificate__content">
    <div class="brand"><span class="brand__dot"></span>Sternenwiege</div>
    <h1 class="title">Sternzertifikat</h1>
    <div class="title-rule"></div>
    <p class="statement">
      Der Stern mit den Koordinaten xx Koordinaten xx<br>
      wurde am 24.09.2022 in das Sternenregister eingetragen.<br>
      Der Stern trägt den Namen
    </p>
    <p class="register">Die Registernummer lautet</p>
  </div>
</main>
</body>
</html>
```